Tech business card design

We need an amazing business card design for our new business 'Pexla' a marketing tech startup based in Sydney, Australia. We provide an online marketplace for businesses to search and buy advertising media, connect with service providers and learn more about marketing. We wish to communicate 'cool tech', reliability and professionalism and design based around our logo.

Target Market(s)

Business Owners

Contact Information for Business Card

Name
Position
Email Address
Website
Phone Number

Font styles to use
Other font styles liked:
• Avenir & Avenir Next

Colors

Designer to choose colors to be used in the design.

```html
<!DOCTYPE html>
<html lang="en">
<head>
<meta charset="utf-8">
<title>Pexla Business Card</title>
<link href="https://fonts.googleapis.com/css2?family=Nunito+Sans:wght@400;600;800&display=swap" rel="stylesheet">
<style>
  :root {
    --backdrop: #ececec;
    --navy: #221f45;
    --paper: #f1f1f1;
    --white: #ffffff;
    --muted: #d9d9e4;
  }
  * { margin: 0; padding: 0; box-sizing: border-box; }
  html, body { width: 1200px; height: 800px; overflow: hidden; }
  body {
    background: var(--backdrop);
    font-family: "Nunito Sans", sans-serif;
    position: relative;
  }
  .card {
    position: absolute;
    top: 279px;
    width: 420px;
    height: 240px;
    background: var(--navy);
    overflow: hidden;
  }
  .card--front { left: 142px; }
  .card--back { left: 637px; }

  .front-band {
    position: absolute;
    left: 0; right: 0;
    top: 42px;
    height: 108px;
    background: var(--paper);
    display: flex;
    align-items: center;
    justify-content: center;
  }
  .wordmark {
    font-weight: 800;
    letter-spacing: -1px;
    line-height: 1;
  }
  .front-band .wordmark {
    color: var(--navy);
    font-size: 78px;
    margin-top: -6px;
  }
  .card--back .wordmark {
    position: absolute;
    left: 46px;
    top: 38px;
    color: var(--white);
    font-size: 52px;
  }
  .identity {
    position: absolute;
    left: 241px;
    top: 47px;
    color: var(--white);
  }
  .identity-name {
    font-size: 19px;
    font-weight: 600;
    letter-spacing: 0.5px;
    line-height: 1.05;
  }
  .identity-role {
    font-size: 12.5px;
    letter-spacing: 0.6px;
    color: var(--muted);
    text-transform: uppercase;
  }
  .contact-list {
    position: absolute;
    left: 47px;
    top: 131px;
    list-style: none;
    color: var(--white);
    font-size: 17px;
  }
  .contact-item {
    display: flex;
    align-items: center;
    height: 24px;
  }
  .contact-icon {
    width: 13px;
    height: 13px;
    margin-right: 12px;
    flex: none;
  }
</style>
</head>
<body>
  <section class="card card--front">
    <div class="front-band">
      <span class="wordmark">pexla</span>
    </div>
  </section>

  <section class="card card--back">
    <span class="wordmark">pexla</span>
    <div class="identity">
      <p class="identity-name">JOHN SMITH</p>
      <p class="identity-role">General Manager</p>
    </div>
    <ul class="contact-list">
      <li class="contact-item">
        <svg class="contact-icon" viewBox="0 0 16 16" aria-hidden="true">
          <circle cx="8" cy="8" r="8" fill="#fff"/>
          <path d="M5.2 4.2l1.4-.2.8 2-1 .8a5 5 0 0 0 2.8 2.8l.8-1 2 .8-.2 1.4c-.2.6-.9.9-1.6.7A7 7 0 0 1 4.5 5.8c-.2-.7.1-1.4.7-1.6z" fill="#221f45"/>
        </svg>
        012 345 6789
      </li>
      <li class="contact-item">
        <svg class="contact-icon" viewBox="0 0 16 16" aria-hidden="true">
          <rect x="0.5" y="3" width="15" height="10" rx="1" fill="#fff"/>
          <path d="M1 4l7 5 7-5" fill="none" stroke="#221f45" stroke-width="1.4"/>
        </svg>
        your@email.com
      </li>
      <li class="contact-item">
        <svg class="contact-icon" viewBox="0 0 16 16" aria-hidden="true">
          <circle cx="8" cy="8" r="7.5" fill="#fff"/>
          <g fill="none" stroke="#221f45" stroke-width="0.9">
            <ellipse cx="8" cy="8" rx="3" ry="7"/>
            <path d="M1 8h14M2 4.5h12M2 11.5h12M8 1v14"/>
          </g>
        </svg>
        www.website.com
      </li>
    </ul>
  </section>
</body>
</html>
```